Fresh, modern, fun business card for pediatric dental practice

Need a business card for fresh, modern, fun pediatric dental practice

Clean look that matches our website's font and colors

We prefer the look of curved corners on business cards

Target Market(s)

parents (mothers) of young children, professionals, mid-high class

Industry/Entity Type

Dental

Contact Information for Business Card

Maplebrook Pediatric Dentistry
482 Quarry Lane
Suite 517
Cedarvale, OH 44907
330.555.0193
www.maplebrookkidsdental.example

Mei-Ran Tsai, DMD
Corinne Walbeck, DMD
(we are working on our email address, but we would like that on the card as well)

Font styles to use
Sans Serif

Requirements
Must have
• All info; we would also like to make cards for individual staff members
• colors from our website and color palatte, attatched
• use same font and design as website for branding
Nice to have
• clean, simple card that has a pop of color
• we would like to see a few designs with our tag line "where every smile shines"
• we are not sure if we want to have it on there or not
• we would like to see a few designs incorporating the ribbon graphic on our website where the word WELCOME is

```html
<!DOCTYPE html>
<html lang="en">
<head>
<meta charset="utf-8">
<title>Maplebrook Pediatric Dentistry – Business Card</title>
<link rel="stylesheet" href="https://fonts.googleapis.com/css2?family=Open+Sans:wght@600&family=Roboto:wght@400&family=Roboto+Condensed:wght@700&display=swap">
<style>
  :root {
    --backdrop: #2c2c2c;
    --card: #f4f4f4;
    --sun: #f9b823;
    --sun-soft: #fdeab8;
    --ink: #4a4a4a;
    --shadow: rgba(0,0,0,0.45);
  }
  * { margin: 0; padding: 0; box-sizing: border-box; }
  html, body { width: 1200px; height: 960px; overflow: hidden; }
  body { background: var(--backdrop); position: relative; font-family: "Roboto", Arial, sans-serif; }

  .card {
    position: absolute;
    width: 598px; height: 342px;
    background: var(--card);
    border-radius: 18px;
    box-shadow: 0 4px 6px var(--shadow);
    overflow: hidden;
  }
  .card--front { left: 322px; top: 108px; }
  .card--back  { left: 320px; top: 493px; }

  .brand { font-family: "Open Sans", Arial, sans-serif; font-weight: 600; color: var(--sun); line-height: 1; }
  .brand__name { display: block; letter-spacing: 1px; }
  .brand__sub { display: block; letter-spacing: 1.5px; }

  /* front */
  .brand-dot {
    position: absolute; left: 285px; top: 88px;
    width: 30px; height: 30px; border-radius: 50%; background: var(--sun);
  }
  .front-brand { position: absolute; left: 0; right: 0; top: 130px; text-align: center; }
  .front-brand .brand__name { font-size: 48px; }
  .front-brand .brand__sub { font-size: 24px; margin-top: 6px; }
  .tagline {
    position: absolute; left: 0; right: 0; top: 288px;
    display: flex; align-items: center; justify-content: center; gap: 4px;
    font-size: 14px; color: var(--ink);
  }
  .tagline::before, .tagline::after { content: ""; width: 38px; height: 1px; background: var(--sun); }

  /* back */
  .back-brand { position: absolute; left: 32px; top: 42px; }
  .back-brand .brand__name { font-size: 42px; }
  .back-brand .brand__sub { font-size: 21px; margin-top: 4px; }
  .doctors {
    position: absolute; left: 32px; top: 124px;
    font-family: "Roboto Condensed", Arial, sans-serif; font-weight: 700;
    font-size: 21px; line-height: 24px; color: var(--sun);
  }
  .address {
    position: absolute; left: 32px; top: 180px;
    font-style: normal; font-size: 14.5px; line-height: 19px; color: var(--ink);
  }
  .contacts { position: absolute; left: 32px; top: 246px; list-style: none; font-size: 14.5px; line-height: 19.5px; color: var(--ink); }
  .contacts li { display: flex; align-items: center; gap: 8px; }
  .contacts svg { width: 13px; height: 13px; fill: var(--sun); flex: none; }

  .decor-area {
    position: absolute; left: 290px; top: 14px; width: 292px; height: 314px;
    border-radius: 50%;
    background: radial-gradient(circle, var(--sun-soft) 0%, rgba(253,234,184,0.35) 60%, rgba(244,244,244,0) 72%);
  }
</style>
</head>
<body>

  <section class="card card--front" aria-label="Business card front">
    <span class="brand-dot" aria-hidden="true"></span>
    <h1 class="brand front-brand">
      <span class="brand__name">maplebrook</span>
      <span class="brand__sub">pediatric dentistry</span>
    </h1>
    <p class="tagline">where every smile shines</p>
  </section>

  <section class="card card--back" aria-label="Business card back">
    <h2 class="brand back-brand">
      <span class="brand__name">maplebrook</span>
      <span class="brand__sub">pediatric dentistry</span>
    </h2>
    <p class="doctors">MEI-RAN TSAI, DMD<br>CORINNE WALBECK, DMD</p>
    <address class="address">
      Maplebrook Pediatric Dentistry<br>
      482 Quarry Lane, Suite 517<br>
      Cedarvale, OH 44907
    </address>
    <ul class="contacts">
      <li>
        <svg viewBox="0 0 24 24" aria-hidden="true"><path d="M6.6 10.8a15.1 15.1 0 0 0 6.6 6.6l2.2-2.2c.3-.3.7-.4 1-.2 1.1.4 2.3.6 3.6.6.6 0 1 .4 1 1V20c0 .6-.4 1-1 1A17 17 0 0 1 3 4c0-.6.4-1 1-1h3.5c.6 0 1 .4 1 1 0 1.3.2 2.5.6 3.6.1.3 0 .7-.2 1z"/></svg>
        330.555.0193
      </li>
      <li>
        <svg viewBox="0 0 24 24" aria-hidden="true"><path d="M2 5h20v14H2zM3.5 6.5 12 13l8.5-6.5z"/></svg>
        info@maplebrookkidsdental.example
      </li>
      <li>
        <svg viewBox="0 0 24 24" aria-hidden="true"><path d="M12 2a10 10 0 1 0 0 20 10 10 0 0 0 0-20zm-1 17.9A8 8 0 0 1 4.1 10.9L9 15.8v1.1c0 1.1.9 2 2 2zm6.9-2.5c-.3-.8-1-1.4-1.9-1.4h-1v-3c0-.6-.4-1-1-1H8v-2h2c.6 0 1-.4 1-1V7h2c1.1 0 2-.9 2-2v-.4a8 8 0 0 1 2.9 12.8z"/></svg>
        maplebrookkidsdental.example
      </li>
    </ul>
    <div class="decor-area" role="img" aria-label="Large brand decoration area in warm yellow"></div>
  </section>

</body>
</html>
```